The most modern business card ever !!!

Our company call “Vendalo”. Vendalo is a technology company specialized in cruises solutions. Out main product is a platform to reserve cruises. This is a revolutionary platform that make easier to travel agencies and final users to reserve cruises across dozen companies like tibba, wernu, hpv, dgb, etc..We are a “start up”, with a young team of developers and we want to transmit it.. For it, we want something different, a modern business card that represent cruises and technology.. When someone receive this card, this person should say: wowww this is different… this is modern… this is a cruise related company..
- diferent, modern
- traditions business card

```html
<!DOCTYPE html>
<html lang="en">
<head>
<meta charset="utf-8">
<title>Vendalo Business Card</title>
<link rel="stylesheet" href="https://fonts.googleapis.com/css2?family=Open+Sans:wght@400;600&display=swap">
<style>
  :root {
    --page-bg: #e6e6e6;
    --card-bg: #050505;
    --logo-grey: #d9d9d9;
    --accent-blue: #1fb3ef;
    --text-white: #f2f2f2;
    --divider: #8a8a8a;
  }
  * { margin: 0; padding: 0; box-sizing: border-box; }
  html, body { width: 1200px; height: 782px; overflow: hidden; }
  body {
    background: var(--page-bg);
    font-family: "Open Sans", sans-serif;
    position: relative;
  }
  .business-card {
    position: absolute;
    left: 180px;
    top: 151px;
    width: 840px;
    height: 480px;
    background: var(--card-bg);
    box-shadow: 0 8px 24px rgba(0,0,0,0.25);
  }
  .brand-name {
    position: absolute;
    top: 120px;
    left: 0;
    width: 100%;
    text-align: center;
    font-size: 84px;
    font-weight: 600;
    letter-spacing: 4px;
    color: var(--logo-grey);
  }
  .contact-area {
    position: absolute;
    top: 318px;
    left: 0;
    width: 100%;
    display: flex;
    justify-content: center;
    align-items: stretch;
  }
  .person-block {
    text-align: right;
    padding-right: 24px;
    font-size: 21px;
    line-height: 28px;
    color: var(--text-white);
  }
  .person-name {
    color: var(--accent-blue);
    font-weight: 600;
    font-size: 22px;
  }
  .divider {
    width: 2px;
    background: var(--divider);
  }
  .contact-list {
    list-style: none;
    padding-left: 24px;
    font-size: 21px;
    line-height: 28px;
    color: var(--text-white);
  }
  .contact-list li { display: flex; align-items: center; gap: 10px; }
  .contact-icon { width: 16px; height: 16px; fill: var(--accent-blue); flex: none; }
</style>
</head>
<body>
  <main class="business-card">
    <div class="brand-name">Vendalo</div>
    <section class="contact-area">
      <div class="person-block">
        <div class="person-name">DANIEL MORENO</div>
        <div class="person-title">Managing Director</div>
        <div class="address">12345, Address Goes Here</div>
        <div class="address">Country Name, 123456</div>
      </div>
      <div class="divider"></div>
      <ul class="contact-list">
        <li>
          <svg class="contact-icon" viewBox="0 0 16 16"><path d="M3 6c0-2 2-3 5-3s5 1 5 3l-2 1-1-2H6L5 7z M4 8h8l1 5H3z"/></svg>
          044-310 872 615
        </li>
        <li>
          <svg class="contact-icon" viewBox="0 0 16 16"><path d="M5 1h6a1 1 0 0 1 1 1v12a1 1 0 0 1-1 1H5a1 1 0 0 1-1-1V2a1 1 0 0 1 1-1zm1 2v9h4V3z"/></svg>
          044-310 872 615
        </li>
        <li>
          <svg class="contact-icon" viewBox="0 0 16 16"><path d="M1 3h14v10H1zm1.5 1.5L8 9l5.5-4.5z"/></svg>
          info@vendalo.com
        </li>
        <li>
          <svg class="contact-icon" viewBox="0 0 16 16"><circle cx="8" cy="8" r="7"/></svg>
          www.vendalo.com
        </li>
      </ul>
    </section>
  </main>
</body>
</html>
```